Menu Design Project

My Restaurant is called The Platter Corner, it's fast food restaurant serves Gyro, Wings, Subs, Fried Seafood and chicken tenders. I'm looking for a menu design to fit the fast food category and have some photos of the food on the front page as well inside the menu. I will attached some photos and you can add any other photo related to the menu from the web.

Industry/Entity Type

Restaurant

```html
<!DOCTYPE html>
<html lang="en">
<head>
<meta charset="utf-8">
<title>The Platter Corner – Menu Cover</title>
<link href="https://fonts.googleapis.com/css2?family=Bebas+Neue&family=Nunito:wght@900&family=Oswald:wght@300;500&family=Roboto:wght@400&display=swap" rel="stylesheet">
<style>
  :root {
    --paper-light: #f6c24a;
    --paper-mid: #efaa36;
    --paper-dark: #e18a25;
    --ink-black: #1a1410;
    --olive: #6b5a14;
    --tangerine: #e9702a;
    --maroon: #6b1422;
    --brand-red: #d8232a;
    --photo-dark: #6b4a30;
    --photo-light: #e9dcc8;
    --map-grey: #eeeeee;
  }
  * { margin: 0; padding: 0; box-sizing: border-box; }
  html, body { width: 927px; height: 1200px; overflow: hidden; }
  body { background: var(--paper-mid); }

  .menu-cover {
    position: relative;
    width: 927px;
    height: 1200px;
    overflow: hidden;
    background: radial-gradient(ellipse at 50% 45%, var(--paper-light) 0%, var(--paper-mid) 60%, var(--paper-dark) 100%);
  }

  .food-photo {
    position: absolute;
    left: 0; top: 0;
    width: 432px; height: 368px;
    border-radius: 0 0 200px 0;
    background: linear-gradient(135deg, var(--photo-light) 0%, #c9a47c 35%, var(--photo-dark) 70%, #8c6a45 100%);
  }

  /* Folded top panel, printed upside down */
  .flip-panel {
    position: absolute;
    left: 0; top: 0;
    width: 927px; height: 560px;
    transform: rotate(180deg);
  }
  .brand-mark {
    position: absolute;
    left: 152px; top: 40px;
    width: 240px; height: 240px;
    display: flex; align-items: center; justify-content: center;
  }
  .brand-mark svg { position: absolute; inset: 0; }
  .brand-mark-name {
    position: relative;
    width: 150px;
    text-align: center;
    font-family: "Nunito", sans-serif;
    font-weight: 900;
    font-size: 26px;
    line-height: 1.05;
    color: var(--brand-red);
  }
  .flip-title {
    position: absolute;
    left: 40px; top: 296px;
    width: 470px;
    text-align: center;
    font-family: "Nunito", sans-serif;
    font-weight: 900;
    font-size: 44px;
    color: var(--ink-black);
    white-space: nowrap;
  }
  .flip-details {
    position: absolute;
    left: 87px; top: 422px;
    width: 280px;
    text-align: center;
    font-family: "Roboto", sans-serif;
    color: var(--maroon);
  }
  .flip-details .address { font-size: 12.5px; }
  .flip-details .phone { font-family: "Oswald", sans-serif; font-weight: 500; font-size: 17px; margin-top: 4px; }
  .flip-details .hours { font-size: 12.5px; margin-top: 4px; }

  .tagline { position: absolute; left: 120px; top: 622px; }
  .tagline-top {
    font-family: "Bebas Neue", sans-serif;
    font-size: 96px;
    line-height: 1;
    color: var(--olive);
    letter-spacing: 1px;
  }
  .tagline-bottom {
    margin-left: 234px;
    margin-top: -16px;
    font-family: "Oswald", sans-serif;
    font-weight: 300;
    font-size: 132px;
    line-height: 1;
    letter-spacing: -3px;
    color: var(--tangerine);
    transform: scaleY(1.12);
    transform-origin: top left;
  }

  .location-map {
    position: absolute;
    left: 35px; top: 855px;
    width: 320px; height: 308px;
    background: var(--map-grey);
  }

  .contact {
    position: absolute;
    left: 415px; top: 842px;
    color: var(--maroon);
  }
  .contact-call {
    font-family: "Oswald", sans-serif;
    font-weight: 500;
    font-size: 25px;
    line-height: 1.08;
  }
  .contact-line {
    font-family: "Oswald", sans-serif;
    font-weight: 300;
    font-size: 15.5px;
    margin-top: 9px;
  }
  .contact-line + .contact-line { margin-top: 8px; }

  .drinks { position: absolute; left: 415px; top: 1022px; width: 360px; }
  .drinks-title {
    font-family: "Bebas Neue", sans-serif;
    font-size: 44px;
    line-height: 1;
    color: var(--olive);
  }
  .drinks-list {
    font-family: "Roboto", sans-serif;
    font-size: 13.5px;
    line-height: 1.32;
    color: var(--ink-black);
    margin-top: 2px;
  }
</style>
</head>
<body>
  <main class="menu-cover">
    <div class="food-photo" role="img" aria-label="Photo of a gyro wrap filled with sliced meat, lettuce, tomato and sauce in paper"></div>

    <section class="flip-panel">
      <div class="brand-mark">
        <svg viewBox="0 0 240 240" aria-hidden="true"><circle cx="120" cy="120" r="100" fill="none" stroke="var(--brand-red)" stroke-width="6"/></svg>
        <span class="brand-mark-name">The Platter Corner</span>
      </div>
      <h2 class="flip-title">The Platter Corner</h2>
      <div class="flip-details">
        <p class="address">4120 Riverbend Blvd, Lakeview, TX 77512</p>
        <p class="phone">713-555-0148</p>
        <p class="hours">Hours: Monday to Sunday 11am-9pm</p>
      </div>
    </section>

    <h1 class="tagline">
      <span class="tagline-top" style="display:block">Good Food,</span>
      <span class="tagline-bottom" style="display:block">Good Mood</span>
    </h1>

    <div class="location-map" role="img" aria-label="Street map showing the restaurant location"></div>

    <section class="contact">
      <p class="contact-call">CALL US FOR PICK UP ORDERS OR CATERING<br>@ 713-555-0148</p>
      <p class="contact-line">4120 RIVERBEND BLVD, LAKEVIEW, TX 77512</p>
      <p class="contact-line">HOURS: MONDAY TO SUNDAY 11AM-9PM</p>
    </section>

    <section class="drinks">
      <h3 class="drinks-title">Drinks</h3>
      <p class="drinks-list">Fizz Cola, Fizz Cola Zero, Lemon Spark, Power Rush, Sunny Orange, Sunny Strawberry, Doc Cherry and more.</p>
    </section>
  </main>
</body>
</html>
```